Modern Business Card For A Digital Advertising Company

I'll be print on the Pell Prints Velour paper http://us.pellprints.com/products/velour/business-cards.html
Need's to be modern and use the color palette of the logo or gray scales. I think integrating the pixelation of the logo in to the card and having it wrap from one side to the other could be interesting. My company provides ad operations, web development, and number of other services to websites around the world. You can see my website at http://www.zantorhq.com
Contact info on the card needs to have
Owen Lasko
President
p.318.204.6637
owen@zantorhq.com
http://www.zantorhq.com
Doesn't necessarily need to be in that order
Website owners
Business

```html
<!DOCTYPE html>
<html lang="en">
<head>
<meta charset="utf-8">
<title>Zantor HQ Business Card</title>
<link rel="stylesheet" href="https://fonts.googleapis.com/css2?family=Open+Sans:wght@400;600;700&family=Tinos:wght@400;700&display=swap">
<style>
  :root {
    --bg: #1e1e1e;
    --card: #ffffff;
    --green: #8cc63f;
    --green-dark: #5e9a28;
    --rule: #2b2b2b;
    --ink: #3a3a3a;
    --ink-soft: #555555;
  }
  * { margin: 0; padding: 0; box-sizing: border-box; }
  html, body { width: 1200px; height: 757px; overflow: hidden; }
  body { background: var(--bg); position: relative; }

  .card {
    position: absolute;
    width: 520px;
    height: 300px;
    background: var(--card);
    box-shadow: 0 14px 30px rgba(0,0,0,.55);
  }

  /* Front */
  .card-front { left: 50px; top: 228px; }
  .band {
    position: absolute; left: 0; right: 0; height: 42px;
    background: linear-gradient(90deg, var(--green-dark), var(--green) 55%, var(--green-dark));
  }
  .band-top { top: 0; }
  .band-bottom { bottom: 0; height: 34px; }
  .rule { position: absolute; left: 0; right: 0; height: 3px; background: var(--rule); }
  .rule-top { top: 46px; }
  .rule-bottom { bottom: 38px; }

  .holder {
    position: absolute; top: 8px; left: 0; right: 0;
    text-align: center; color: #fff;
    font-family: "Tinos", serif; font-size: 21px; font-weight: 700;
  }
  .holder .title { font-weight: 400; font-size: 17px; }

  .brand {
    position: absolute; top: 88px; left: 0; right: 0;
    display: flex; justify-content: center; align-items: center; gap: 10px;
    font-family: "Open Sans", sans-serif; font-weight: 700;
    font-size: 34px; letter-spacing: 2px; color: var(--ink);
  }
  .brand-mark { width: 26px; height: 26px; background: var(--green); }

  .contact {
    position: absolute; top: 162px; left: 0; right: 0;
    font-family: "Tinos", serif; font-size: 16px; color: var(--ink);
    text-align: center; line-height: 26px;
  }
  .contact-row { display: flex; justify-content: center; gap: 18px; }
  .contact-item { display: inline-flex; align-items: center; gap: 5px; }
  .contact-item svg { width: 13px; height: 13px; fill: var(--ink); }

  /* Back */
  .card-back { left: 630px; top: 228px; }
  .back-brand {
    position: absolute; top: 62px; left: 0; right: 0;
    display: flex; justify-content: center; align-items: center; gap: 10px;
    font-family: "Open Sans", sans-serif; font-weight: 700;
    font-size: 34px; letter-spacing: 2px; color: var(--ink);
  }
  .services-title {
    position: absolute; top: 140px; left: 0; right: 0; text-align: center;
    font-family: "Open Sans", sans-serif; font-weight: 700;
    font-size: 22px; letter-spacing: 2px; color: var(--ink);
  }
  .services {
    position: absolute; top: 178px; left: 0; right: 0;
    list-style: none; text-align: center;
    font-family: "Open Sans", sans-serif; font-size: 14px; color: var(--ink-soft);
    line-height: 21px;
  }
  .services li { display: inline-block; margin: 0 7px; }
  .services li::before { content: "•"; color: var(--green); margin-right: 5px; }
  .services .row { display: block; }
</style>
</head>
<body>

<section class="card card-front" aria-label="Card front">
  <div class="band band-top"></div>
  <div class="rule rule-top"></div>
  <p class="holder">Owen Lasko, <span class="title">President</span></p>

  <div class="brand"><span class="brand-mark"></span>ZANTOR HQ</div>

  <div class="contact">
    <div class="contact-row">
      <span class="contact-item">
        <svg viewBox="0 0 16 16" aria-hidden="true"><path d="M3.6 1.5l2.3 2.8-1.3 1.8c.9 2 2.4 3.6 4.5 4.6l1.8-1.3 2.8 2.3-1.4 2.3C7 13.4 2.6 9 1.3 3.1z"/></svg>
        318.204.6637
      </span>
      <span class="contact-item">
        <svg viewBox="0 0 16 16" aria-hidden="true"><path d="M1 4h14v9H1zM2 5l6 4.5L14 5v-.5H2z"/></svg>
        owen@zantorhq.com
      </span>
    </div>
    <div class="contact-row">
      <span class="contact-item">
        <svg viewBox="0 0 16 16" aria-hidden="true"><circle cx="8" cy="8" r="7"/></svg>
        www.zantorhq.com
      </span>
    </div>
  </div>

  <div class="rule rule-bottom"></div>
  <div class="band band-bottom"></div>
</section>

<section class="card card-back" aria-label="Card back">
  <div class="back-brand"><span class="brand-mark"></span>ZANTOR HQ</div>
  <h2 class="services-title">Services</h2>
  <ul class="services">
    <span class="row"><li>Ad Operations</li><li>Web Development</li></span>
    <span class="row"><li>Hosting</li><li>Site Speed</li></span>
    <span class="row"><li>Social Media</li></span>
    <span class="row"><li>Search Engine Optimization</li></span>
  </ul>
</section>

</body>
</html>
```